Emergency and Referral Vet Hospital promotional sticker design

We're looking at getting some stickers designed that we could give to clients to put on their cars for promotion and advertising. If they could also be suitable for a goodie bag for conference too that would be great. I like the look of water-colour backgrounds, we'll need to include our logo and probably our address (Unit 3/215 Korrinup Road Tallowmere). We also have a hospital motto "... because they're family" if that could somehow be integrated, we only care for small animals (dogs, cats etc) but the design is very open to suggestion. Would love to see what you can create.

Industry/Entity Type

Veterinary

Colors
0054AA
0677BA
7BADD7
CADEEF
E8F1F8
0094D4
00A9DD
6FCCEA
C7EBF8
E9F6FB

Requirements
Nice to have
• Think beach vibes, blues maybe paw print shapes etc

```html
<!DOCTYPE html>
<html lang="en">
<head>
<meta charset="utf-8">
<title>Tidewell Vet – Comprehensive Veterinary Care</title>
<link rel="stylesheet" href="https://fonts.googleapis.com/css2?family=Poppins:wght@500;600&family=EB+Garamond:wght@700&family=Oswald:wght@500&display=swap">
<style>
  :root {
    --ink: #0a0a0a;
    --brand-blue: #0054AA;
    --mid-blue: #0677BA;
    --soft-blue: #7BADD7;
    --pale-blue: #CADEEF;
    --mist: #E8F1F8;
    --white: #ffffff;
  }
  html, body { margin: 0; padding: 0; overflow: hidden; }
  body { width: 1200px; height: 800px; background: var(--white); }
  .sticker {
    position: relative;
    width: 1200px;
    height: 800px;
    overflow: hidden;
    background: var(--white);
    font-family: "Poppins", sans-serif;
  }
  .headline {
    position: absolute;
    left: 64px;
    top: 78px;
    margin: 0;
    font-weight: 600;
    font-size: 62px;
    line-height: 78px;
    letter-spacing: -0.5px;
    color: var(--ink);
  }
  .headline .accent { color: var(--brand-blue); }
  .brand {
    position: absolute;
    left: 985px;
    top: 58px;
    width: 140px;
    display: flex;
    flex-direction: column;
    align-items: center;
    gap: 12px;
  }
  .brand-dot {
    width: 78px;
    height: 78px;
    border-radius: 50%;
    background: var(--mid-blue);
  }
  .brand-name {
    font-weight: 600;
    font-size: 31px;
    line-height: 1;
    color: var(--ink);
  }
  .pets-photo {
    position: absolute;
    left: 495px;
    top: 225px;
    width: 705px;
    height: 330px;
    border-radius: 120px 120px 0 0;
    background:
      radial-gradient(ellipse at 50% 45%, #e8d3b8 0%, #b58a5c 35%, transparent 65%),
      linear-gradient(90deg, #3a3330 0%, #2a2624 22%, #c9a07a 45%, #f2ece4 55%, #8e8c88 72%, #d7a066 88%, #efe6dc 100%);
    opacity: 0.95;
  }
  .wave { position: absolute; left: 0; top: 0; width: 1200px; height: 800px; }
  .motto {
    position: absolute;
    left: 64px;
    top: 530px;
    margin: 0;
    font-family: "EB Garamond", serif;
    font-weight: 700;
    font-size: 92px;
    line-height: 116px;
    color: var(--white);
    text-shadow: 0 3px 8px rgba(0, 30, 80, 0.35);
  }
  .contact {
    position: absolute;
    left: 697px;
    top: 590px;
    color: var(--white);
  }
  .contact-row { display: flex; align-items: center; gap: 14px; }
  .contact-icon { width: 54px; height: 54px; flex: none; }
  .phone {
    font-family: "Oswald", sans-serif;
    font-weight: 500;
    font-size: 60px;
    line-height: 1;
    letter-spacing: -0.5px;
  }
  .address {
    margin-top: 30px;
    font-weight: 500;
    font-size: 26px;
    line-height: 34px;
  }
</style>
</head>
<body>
<main class="sticker">
  <h1 class="headline">Comprehensive<br><span class="accent">Veterinary care</span><br>for your pets</h1>

  <div class="brand">
    <div class="brand-dot"></div>
    <div class="brand-name">tidewell</div>
  </div>

  <div class="pets-photo" role="img" aria-label="Photo of a row of puppies and kittens looking at the camera"></div>

  <svg class="wave" viewBox="0 0 1200 800" aria-hidden="true">
    <defs>
      <linearGradient id="band-fill" x1="0" y1="0.3" x2="1" y2="0.9">
        <stop offset="0" stop-color="#0054AA"/>
        <stop offset="0.55" stop-color="#0677BA"/>
        <stop offset="1" stop-color="#7BADD7"/>
      </linearGradient>
    </defs>
    <path d="M0 447 C 120 420, 240 412, 380 432 C 560 460, 720 520, 900 525 C 1020 528, 1120 510, 1200 500 L1200 800 L0 800 Z" fill="#6A9ED2"/>
    <path d="M0 497 C 110 470, 250 455, 400 470 C 600 492, 760 535, 920 538 C 1040 540, 1130 518, 1200 505 L1200 800 L0 800 Z" fill="url(#band-fill)"/>
  </svg>

  <p class="motto">...Because<br>they're family</p>

  <div class="contact">
    <div class="contact-row">
      <svg class="contact-icon" viewBox="0 0 54 54" aria-hidden="true">
        <circle cx="27" cy="27" r="25" fill="none" stroke="#fff" stroke-width="2.5"/>
        <path d="M19 18 l5 -2 l3 6 l-3 2 c1 4 4 7 8 8 l2 -3 l6 3 l-2 5 c-10 0 -19 -9 -19 -19 z" fill="none" stroke="#fff" stroke-width="2.4" stroke-linejoin="round"/>
      </svg>
      <div class="phone">(08) 9387 2140</div>
    </div>
    <div class="contact-row">
      <svg class="contact-icon" viewBox="0 0 54 54" aria-hidden="true">
        <circle cx="27" cy="27" r="25" fill="none" stroke="#fff" stroke-width="2.5"/>
        <path d="M27 40 C 20 31, 18 27, 18 23 a9 9 0 0 1 18 0 c0 4 -2 8 -9 17 z" fill="#fff"/>
        <circle cx="27" cy="23" r="3.5" fill="#0677BA"/>
      </svg>
      <div class="address">Unit 3, 215 Korrinup Road<br>Tallowmere, WA 6172</div>
    </div>
  </div>
</main>
</body>
</html>
```